Manuka Honey company needs a Upmarket, Luxury Website!

New Zealand, Taranaki based Manuka Honey company Rimu Vale Honey is looking for a new website, we are looking for an upmarket, luxury, serious website design. We export the highest quality quality Manuka Honey, straight from the Taranaki region.

Main export markets are Asia & Europe, also New Zealand & Australia.

Looking to have a beautiful, upmarket, serious, luxurious & graphical experience with mobile optimization in mind. Like the use of product staging/mockups

You can use copy from other websites to build the site and we will change the copy after the design is finished.

***Please include 'Honey Product' mockups in website.

*Will add illustrator files in coming days***

Feel free to make website functional in Shopify, Wordpress or WIX

Target Market(s)

Asia, Europe (main markets) New Zealand, Australia (Submarkets)

Coding

Coded - Design and coding required

Number of Pages Required

4 page

Requirements
Must have
• Home, Shop, About Us, Contact Us

Homepage to include:

Our Products
Company Video (video under construction)
What is MGO/KPS
Newsletter Opt-in

***(Not in Order)***

Please include 'Honey Product' mockups in website.
*Will add illustrator files in coming days
Nice to have
• FAQ & Partnership Inquiries (hyperlink in footer)

```html
<!DOCTYPE html>
<html lang="en">
<head>
<meta charset="utf-8">
<title>Rimu Vale Honey — Manuka Honey</title>
<link rel="stylesheet" href="https://fonts.googleapis.com/css2?family=Jost:wght@400;500;600;700&family=Montserrat:wght@400;500;600&display=swap">
<style>
:root{
  --ink:#1c1c1c;
  --text:#4a4a4a;
  --gold:#c9a45a;
  --gold-light:#f1e79c;
  --cream:#f7efe0;
  --hero-top:#e6cf93;
  --hero-bottom:#f4ecaa;
  --amber:#8a5a1e;
  --amber-soft:#c99a4a;
  --dark-card:#262626;
  --white:#ffffff;
  --black:#000000;
}
*{margin:0;padding:0;box-sizing:border-box}
html,body{width:1200px;height:3838px;overflow:hidden}
body{position:relative;background:var(--white);font-family:"Montserrat",sans-serif;color:var(--text)}
.abs{position:absolute}
.heading{font-family:"Jost",sans-serif;font-weight:600;letter-spacing:4px;color:var(--ink);text-transform:uppercase;white-space:nowrap}
.btn{position:absolute;display:flex;align-items:center;justify-content:center;border-radius:30px;font-family:"Jost",sans-serif;font-weight:600;letter-spacing:2px;text-transform:uppercase;color:var(--ink);background:linear-gradient(90deg,var(--gold),var(--gold-light));white-space:nowrap}
.body-copy{font-size:13.5px;line-height:23.5px;color:var(--text)}
.arrow{position:absolute;width:30px;height:50px}
.arrow path{fill:none;stroke:#555;stroke-width:3.5;stroke-linecap:round;stroke-linejoin:round}

/* header */
.brand{position:absolute;display:flex;align-items:center;gap:12px;font-family:"Jost",sans-serif;font-weight:500;font-size:27px;letter-spacing:3px;color:#3a3a3a;white-space:nowrap}
.brand-dot{width:34px;height:34px;border-radius:50%;background:var(--gold)}
.nav{position:absolute;left:582px;top:37px;display:flex;font-size:13px;color:var(--ink);white-space:nowrap}
.nav a{color:var(--ink);text-decoration:none}
.nav .sep{margin:0 40px}
.nav .active{font-weight:600}

/* hero */
.hero{left:0;top:0;width:1200px;height:760px;background:linear-gradient(180deg,var(--hero-top),var(--hero-bottom) 70%,#f6eebc)}
.hero-product{left:127px;top:190px;width:476px;height:400px;border-radius:24px;background:radial-gradient(ellipse at 50% 50%,rgba(90,55,20,.55),rgba(201,154,74,.35) 55%,rgba(240,225,160,0) 78%)}
.hero-title{left:666px;top:245px;font-family:"Jost",sans-serif;font-weight:700;font-size:84px;line-height:68px;letter-spacing:6px;color:var(--black)}
.hero-tag{left:666px;top:395px;font-family:"Jost",sans-serif;font-size:28px;letter-spacing:3px;color:var(--ink);white-space:nowrap}
.hero .btn{left:666px;top:452px;width:174px;height:48px;background:var(--ink);color:var(--gold-light);font-size:13px}

/* mgo */
.mgo-title{left:131px;top:850px;font-size:38px}
.mgo-copy{left:131px;top:913px;width:462px}
.mgo-copy p+p{margin-top:23px}
.mgo .btn{left:131px;top:1125px;width:187px;height:48px;font-size:14px}
.emblem{left:638px;top:790px;width:477px;height:425px;border-radius:50% 50% 50% 50% / 40% 40% 60% 60%;background:radial-gradient(circle at 50% 55%,#e7cf80,#f6ecc3 55%,#ffffff 72%)}

/* products */
.products{left:0;top:1289px;width:1200px;height:596px;background:linear-gradient(135deg,#f3e6cf,#f8f1e4 45%,#f1e4c8)}
.products-title{left:0;top:1346px;width:1200px;text-align:center;font-size:32px}
.product-card-active{left:377px;top:1435px;width:241px;height:359px;background:#fdf8f0;box-shadow:0 4px 18px rgba(120,90,40,.15)}
.product{position:absolute;width:220px;text-align:center}
.product-image{position:absolute;left:50px;top:0;width:120px;height:180px;border-radius:14px;background:radial-gradient(ellipse at 50% 50%,rgba(90,55,20,.45),rgba(201,154,74,.25) 60%,rgba(240,225,160,0) 85%)}
.product h3{position:absolute;top:210px;left:0;width:220px;font-family:"Jost",sans-serif;font-weight:500;font-size:19px;color:var(--ink);white-space:nowrap}
.product p{position:absolute;top:236px;left:0;width:220px;font-size:11px;color:#666;white-space:nowrap}
.product .btn{top:262px;left:36px;width:148px;height:40px;font-size:11px}

/* about */
.about-bg{left:0;top:1890px;width:1200px;height:576px;background:linear-gradient(180deg,#fff,#f6f6f4 55%,#fff)}
.video{left:100px;top:1995px;width:499px;height:334px;background:linear-gradient(135deg,#8a7a55,#c9c2a6 45%,#e9e8e2 60%,#6f6a4e);box-shadow:0 6px 20px rgba(0,0,0,.2)}
.video-label{left:100px;top:2148px;width:499px;text-align:center;font-family:"Jost",sans-serif;font-weight:600;font-size:17px;letter-spacing:3px;color:var(--white)}
.play{left:100px;top:2282px;width:64px;height:47px;background:var(--gold-light);display:flex;align-items:center;justify-content:center}
.about-title{left:662px;top:2005px;font-size:34px}
.about-copy{left:666px;top:2068px;width:430px}
.about-copy p+p{margin-top:23px}
.about .btn{left:666px;top:2270px;width:188px;height:48px;font-size:14px}

/* testimonials */
.testimonials{left:0;top:2466px;width:1200px;height:520px}
.testimonials-title{left:0;top:2520px;width:1200px;text-align:center;font-size:32px;color:var(--white)}
.quote-card{position:absolute;top:2645px;width:305px;height:256px;border:1px solid rgba(255,255,255,.6);padding:72px 44px 0}
.quote-card.featured{background:var(--dark-card);border-color:var(--dark-card)}
.quote-card p{font-size:11.5px;line-height:19px;color:#fff4d0}
.quote-card .who{margin-top:16px;font-family:"Jost",sans-serif;font-weight:700;font-size:11px;letter-spacing:1px;color:#fff4d0}
.avatar{position:absolute;top:2589px;width:107px;height:107px;border-radius:50%;background:linear-gradient(160deg,#b9a27d,#6d5a44);border:3px solid rgba(255,255,255,.7)}

/* newsletter */
.newsletter-bg{left:0;top:2980px;width:1200px;height:420px;background:radial-gradient(ellipse at 50% 30%,#faf7f0,#fff 70%)}
.newsletter-title{left:0;top:3094px;width:1200px;text-align:center;font-size:31px;color:var(--black)}
.newsletter-sub{left:0;top:3147px;width:1200px;text-align:center;font-size:14px;color:#555}
.signup{left:304px;top:3186px;width:595px;height:58px;border:1px solid #bbb;border-radius:30px}
.signup span{position:absolute;left:34px;top:19px;font-size:14px;color:#555}
.signup .btn{left:408px;top:3px;width:178px;height:50px;font-size:15px}

/* footer */
.footer{left:0;top:3323px;width:1200px;height:515px}
.footer-brand{left:134px;top:3535px;font-family:"Jost",sans-serif;font-weight:600;font-size:20px;letter-spacing:2px;color:var(--gold-light)}
.footer-col{position:absolute;top:3486px}
.footer-col h4{font-family:"Jost",sans-serif;font-weight:600;font-size:15px;letter-spacing:2px;color:var(--white);white-space:nowrap}
.footer-col h4::after{content:"";display:block;width:28px;height:3px;background:var(--gold);margin-top:9px}
.footer-col ul{list-style:none;margin-top:13px}
.footer-col li{font-size:13px;line-height:30px;color:#ddd}
.footer-col .note{margin-top:14px;font-size:13px;color:#ddd}
.footer-input{margin-top:10px;width:232px;height:35px;background:var(--white);font-size:10px;color:#555;padding:11px 18px}
.footer-sub{margin-top:10px;width:232px;height:39px;background:linear-gradient(90deg,var(--gold),var(--gold-light));font-size:12px;font-weight:600;color:var(--ink);display:flex;align-items:center;justify-content:center}
.divider{left:0;top:3767px;width:1200px;height:1px;background:#333}
.copyright{left:0;top:3790px;width:1200px;text-align:center;font-size:12px;color:var(--gold-light)}
</style>
</head>
<body>

<!-- HERO -->
<section class="hero-wrap">
  <div class="abs hero">
    <div class="abs hero-product" role="img" aria-label="Product mockup of three Manuka honey jars before a mountain landscape"></div>
    <h1 class="abs hero-title">MANUKA<br>HONEY</h1>
    <p class="abs hero-tag">TASTE NEVER NEVER BEFORE</p>
    <a class="btn">Learn More</a>
    <svg class="arrow" style="left:45px;top:340px" viewBox="0 0 30 50"><path d="M24 4 L6 25 L24 46"/></svg>
    <svg class="arrow" style="left:1118px;top:340px" viewBox="0 0 30 50"><path d="M6 4 L24 25 L6 46"/></svg>
    <svg class="abs" style="left:0;top:660px" width="1200" height="100" viewBox="0 0 1200 100"><path d="M0 80 C220 110 420 70 700 40 C900 20 1060 15 1200 35 L1200 100 L0 100 Z" fill="#fff"/></svg>
  </div>
  <div class="brand" style="left:90px;top:26px"><span class="brand-dot"></span>RIMU VALE HONEY</div>
  <nav class="nav">
    <a class="active">HOME</a><span class="sep">|</span>
    <a>SHOP</a><span class="sep">|</span>
    <a>ABOUT US</a><span class="sep">|</span>
    <a>CONTACT US</a>
  </nav>
</section>

<!-- WHAT IS MGO -->
<section class="mgo">
  <h2 class="abs heading mgo-title">What is MGO</h2>
  <div class="abs body-copy mgo-copy">
    <p>Lorem Ipsum is simply dummy text of the printing and typesetting industry. Lorem Ipsum has been the industry's standard dummy text ever since the 1500s, when an unknown printer took a galley of type and scrambled it to make a type specimen book. It has</p>
    <p>was popularised in the 1960s with the release of Typeline sheets containing Lorem Ipsum passages, and more recently with desktop publishing software like Folio Setter including version</p>
  </div>
  <a class="btn">Learn More</a>
  <div class="abs emblem" role="img" aria-label="Large decorative gold emblem artwork"></div>
</section>

<!-- PRODUCTS -->
<section>
  <div class="abs products" role="img" aria-label="Soft cream background of manuka blossom"></div>
  <h2 class="abs heading products-title">Our Products</h2>
  <div class="abs product-card-active"></div>
  <div class="product" style="left:152px;top:1465px"><div class="product-image" role="img" aria-label="Honey jar product mockup"></div><h3>Harvest Honey</h3><p>Lorem Ipsum is simply dummy</p><a class="btn" style="top:258px">Learn More</a></div>
  <div class="product" style="left:389px;top:1465px"><div class="product-image" role="img" aria-label="Honey jar product mockup"></div><h3>Harvest Honey</h3><p>Lorem Ipsum is simply dummy</p><a class="btn">Learn More</a></div>
  <div class="product" style="left:628px;top:1465px"><div class="product-image" role="img" aria-label="Honey jar product mockup"></div><h3>Harvest Honey</h3><p>Lorem Ipsum is simply dummy</p><a class="btn" style="top:270px">Learn More</a></div>
  <div class="product" style="left:866px;top:1465px"><div class="product-image" role="img" aria-label="Honey jar product mockup"></div><h3>Harvest Honey</h3><p>Lorem Ipsum is simply dummy</p><a class="btn">Learn More</a></div>
  <svg class="arrow" style="left:108px;top:1552px" viewBox="0 0 30 50"><path d="M24 4 L6 25 L24 46"/></svg>
  <svg class="arrow" style="left:1102px;top:1552px" viewBox="0 0 30 50"><path d="M6 4 L24 25 L6 46"/></svg>
</section>

<!-- ABOUT -->
<section class="about">
  <div class="abs about-bg" role="img" aria-label="Faint misty mountain landscape"></div>
  <div class="abs video" role="img" aria-label="Video still of a bee on a white manuka flower"></div>
  <p class="abs video-label">PLAY VIDEO</p>
  <div class="abs play"><svg width="18" height="22" viewBox="0 0 18 22"><path d="M2 1 L17 11 L2 21 Z" fill="#111"/></svg></div>
  <h2 class="abs heading about-title">About Our Company</h2>
  <div class="abs body-copy about-copy">
    <p>Lorem Ipsum is simply dummy text of the printing and typesetting industry. Lorem Ipsum has been the industry's standard dummy text ever since the 1500s, when an unknown printer took a galley of type and scrambled it to make</p>
    <p>was popularised in the 1960s with the release of Typeline sheets containing Lorem Ipsum passages, and more recently</p>
  </div>
  <a class="btn">Learn More</a>
</section>

<!-- TESTIMONIALS -->
<section>
  <svg class="abs testimonials" viewBox="0 0 1200 520" width="1200" height="520">
    <defs><linearGradient id="tGrad" x1="0" y1="0" x2="1" y2="0"><stop offset="0" stop-color="#d3b16c"/><stop offset="1" stop-color="#e8d592"/></linearGradient></defs>
    <path d="M0 0 H1200 V478 C1000 500 800 505 560 500 C320 495 150 470 0 485 Z" fill="url(#tGrad)"/>
    <path d="M0 485 C150 470 320 495 560 500 C800 505 1000 500 1200 478 V520 H0 Z" fill="#fff"/>
  </svg>
  <h2 class="abs heading testimonials-title">What People Says</h2>
  <div class="quote-card" style="left:124px"><p>Augiat in pede Fusce tellus Sed metus augue convallis et vehicula ut pulvinar eu ante Integer orci tellus tris Aultricies orci ac feugiat suscipit leo massa sodales velit et scelerisque mi tortor at ipsum Proin orci odio commodo</p><p class="who">AROHA LANE</p></div>
  <div class="quote-card featured" style="left:456px"><p>Augiat in pede Fusce tellus Sed metus augue convallis et vehicula ut pulvinar eu ante Integer orci tellus tris Aultricies orci ac feugiat suscipit leo massa sodales velit et scelerisque mi tortor at ipsum Proin orci odio commodo</p><p class="who">AROHA LANE</p></div>
  <div class="quote-card" style="left:784px"><p>Augiat in pede Fusce tellus Sed metus augue convallis et vehicula ut pulvinar eu ante Integer orci tellus tris Aultricies orci ac feugiat suscipit leo massa sodales velit et scelerisque mi tortor at ipsum Proin orci odio commodo</p><p class="who">AROHA LANE</p></div>
  <div class="avatar" style="left:223px" role="img" aria-label="Customer portrait"></div>
  <div class="avatar" style="left:555px" role="img" aria-label="Customer portrait"></div>
  <div class="avatar" style="left:883px" role="img" aria-label="Customer portrait"></div>
  <svg class="arrow" style="left:64px;top:2742px" viewBox="0 0 30 50"><path d="M24 4 L6 25 L24 46" style="stroke:#fff"/></svg>
  <svg class="arrow" style="left:1120px;top:2742px" viewBox="0 0 30 50"><path d="M6 4 L24 25 L6 46" style="stroke:#fff"/></svg>
</section>

<!-- NEWSLETTER -->
<section>
  <div class="abs newsletter-bg" role="img" aria-label="Faint line drawing of manuka blossoms"></div>
  <h2 class="abs heading newsletter-title">Sign Up For Our Newsletter</h2>
  <p class="abs newsletter-sub">Lorem Ipsum is simply dummy text of the printing and typesetting industry.</p>
  <div class="abs signup"><span>Enter Your Email address</span><a class="btn">Subscribe</a></div>
</section>

<!-- FOOTER -->
<footer>
  <svg class="abs footer" viewBox="0 0 1200 515" width="1200" height="515">
    <path d="M0 0 C200 60 420 95 640 88 C860 80 1040 40 1200 30 V515 H0 Z" fill="#000"/>
    <path d="M60 40 C260 95 460 112 680 100 C900 88 1060 50 1200 40" fill="none" stroke="#e8d58a" stroke-width="6"/>
  </svg>
  <div class="abs footer-brand">RIMU VALE<br>HONEY</div>
  <div class="footer-col" style="left:387px">
    <h4>NAVIGATION</h4>
    <ul><li>Home</li><li>About Us</li><li>Products</li><li>Videos</li><li>Cotnact Us</li></ul>
  </div>
  <div class="footer-col" style="left:605px">
    <h4>USEFUL LINKS</h4>
    <ul><li>FAQ</li><li>Partnership Inquiries</li><li>Terms</li><li>Shipping &amp; Return</li><li>Cart</li></ul>
  </div>
  <div class="footer-col" style="left:860px">
    <h4>NEWSLETTER SIGN UP</h4>
    <p class="note">Sign up here to stay up to date</p>
    <div class="footer-input">EMAIL ADDRESS</div>
    <div class="footer-sub">SUBSCRIBE</div>
  </div>
  <div class="abs divider"></div>
  <p class="abs copyright">Copyright © 2021 Rimu Vale Honey</p>
</footer>

</body>
</html>
```